FinTech company looking to revamp and expand client-facing interface for our financial models

Pellworth Engines currently has a very simple website that allows clients to interact with our financial models. We are looking to completely redesign the current site and add several extra pages to provide extra functionality. We want the design to have a modern, slick feel, that will work on both a desktop or a tablet. It should be straightforward for clients to move between different pages at any time, and clear from the layout how to interact with the more advanced features. We have included screenshots of existing pages in the attached design brief, as well as sketches of the functionality required by the new pages, but can't provide a direct link to the current site.
Target Market(s)
Professional investors that will be paying to access the interface
Industry/Entity Type
Finance
Number of Pages Required
4 page
Colors
Designer to choose colors to be used in the design.
Look and feel
Each slider illustrates characteristics of the customer's brand and the style your logo design should communicate.

```html
<!DOCTYPE html>
<html lang="en">
<head>
<meta charset="utf-8">
<title>Pellworth Engines – Models</title>
<link rel="stylesheet" href="https://fonts.googleapis.com/css2?family=Open+Sans:wght@400;600;700&family=Roboto+Condensed:wght@400;500&display=swap">
<style>
  :root {
    --frame: #e3e3e3;
    --white: #ffffff;
    --ink: #111111;
    --navy: #0b386b;
    --charcoal: #333333;
    --header-grey: #666666;
    --row-alt: #f3f3f3;
    --line: #e2e2e2;
    --input-border: #c9c9c9;
    --link: #1a3f87;
  }
  * { box-sizing: border-box; margin: 0; padding: 0; }
  html, body { width: 1200px; height: 715px; overflow: hidden; }
  body {
    background: var(--frame);
    font-family: "Open Sans", Arial, sans-serif;
    color: var(--ink);
    position: relative;
  }
  .app {
    position: absolute; left: 14px; top: 14px; width: 1172px; height: 687px;
    background: linear-gradient(180deg, #efefef 0%, #f6f6f6 40%, #f2f2f2 80%, #d9d9d9 100%);
  }
  /* Top bar */
  .topbar {
    position: absolute; left: 0; top: 0; width: 1172px; height: 55px;
    background: var(--white); display: flex; align-items: stretch;
  }
  .brand {
    width: 166px; padding-left: 53px; display: flex; align-items: center;
    font-weight: 700; font-size: 17px; letter-spacing: 0.2px;
  }
  .horizon { display: flex; }
  .horizon a, .mainnav a {
    display: flex; align-items: center; justify-content: center; gap: 8px;
    text-decoration: none; color: var(--ink); font-weight: 700; font-size: 13px;
    border-right: 1px solid var(--line);
  }
  .horizon a { width: 83px; }
  .horizon a.is-active, .mainnav a.is-active { background: var(--charcoal); color: var(--white); }
  .mainnav { display: flex; margin-left: auto; }
  .mainnav a { font-size: 12.5px; }
  .mainnav .nav-models { width: 130px; }
  .mainnav .nav-sens { width: 163px; }
  .mainnav .nav-fav { width: 182px; border-right: 0; }
  .mainnav svg { width: 22px; height: 22px; }

  /* Category tabs */
  .tabs { position: absolute; left: 51px; top: 92px; display: flex; gap: 5px; }
  .tab {
    width: 143px; height: 51px; background: var(--white);
    display: flex; align-items: center; justify-content: center;
    font-weight: 600; font-size: 13.5px; color: var(--charcoal);
    border-radius: 4px 4px 0 0;
  }
  .tab.is-active { width: 143px; }
  .tab-more { width: 37px; }
  .tab-add {
    width: 37px; height: 51px; background: var(--navy); border-radius: 4px 4px 0 0;
    display: flex; align-items: center; justify-content: center;
  }

  /* Panel */
  .panel {
    position: absolute; left: 0; top: 143px; width: 1172px; height: 544px;
    background: linear-gradient(180deg, #ffffff 0%, #fbfbfb 50%, rgba(245,245,245,0) 100%);
  }
  .filters {
    position: absolute; left: 53px; top: 60px; width: 1082px; height: 30px;
    display: flex; align-items: center; font-size: 16px;
  }
  .filters label { display: flex; align-items: center; }
  .filters b { font-weight: 700; margin-left: 14px; margin-right: 12px; }
  .filters .field {
    width: 167px; height: 29px; border: 1px solid var(--input-border); border-radius: 4px;
    padding: 0 10px; font: 16px "Open Sans", Arial, sans-serif; color: var(--ink); background: var(--white);
  }
  .filters .abs { margin-left: 40px; }
  .export {
    margin-left: auto; display: flex; align-items: center; gap: 6px;
    color: var(--link); font-weight: 700; font-size: 16px; text-decoration: none;
  }

  /* Table */
  .models {
    position: absolute; left: 51px; top: 115px; width: 1070px;
    border-collapse: separate; border-spacing: 0; table-layout: fixed;
    font-family: "Roboto Condensed", "Arial Narrow", sans-serif; font-size: 15.5px;
    background: var(--white); border-radius: 6px; overflow: hidden;
  }
  .models th {
    height: 65px; color: var(--white); font-family: "Open Sans", Arial, sans-serif;
    font-weight: 600; font-size: 16px; background: var(--header-grey);
    border-right: 1px solid #7a7a7a;
  }
  .models th.key { background: var(--navy); border-right-color: #24507f; }
  .models th:last-child { border-right: 0; }
  .models td {
    height: 64.6px; padding: 0 8px; border-right: 1px solid var(--line); line-height: 1.25;
  }
  .models td:last-child { border-right: 0; }
  .models td.num { text-align: center; padding: 0 2px; }
  .models td.num.left { text-align: left; padding-left: 8px; }
  .models td.id { text-align: center; }
  .models td.time { text-align: center; }
  .models tbody tr:nth-child(even) td { background: var(--row-alt); }
</style>
</head>
<body>
<div class="app">
  <header class="topbar">
    <div class="brand">QVANTA</div>
    <nav class="horizon">
      <a href="#" class="is-active">250D</a>
      <a href="#">83D</a>
      <a href="#">42D</a>
    </nav>
    <nav class="mainnav">
      <a href="#" class="nav-models is-active">
        <svg viewBox="0 0 24 24" fill="none" stroke="#fff" stroke-width="2"><path d="M3 11 12 3l9 8"/><path d="M5 10v10h5v-6h4v6h5V10"/></svg>
        MODELS</a>
      <a href="#" class="nav-sens">
        <svg viewBox="0 0 24 24" fill="#222"><circle cx="12" cy="12" r="2.2"/><circle cx="12" cy="4" r="1.5"/><circle cx="12" cy="20" r="1.5"/><circle cx="4" cy="12" r="1.5"/><circle cx="20" cy="12" r="1.5"/><circle cx="6.3" cy="6.3" r="1.5"/><circle cx="17.7" cy="17.7" r="1.5"/><circle cx="17.7" cy="6.3" r="1.5"/><circle cx="6.3" cy="17.7" r="1.5"/><circle cx="12" cy="8" r="1"/><circle cx="12" cy="16" r="1"/><circle cx="8" cy="12" r="1"/><circle cx="16" cy="12" r="1"/></svg>
        SENSITIVITIES</a>
      <a href="#" class="nav-fav">
        <svg viewBox="0 0 24 24" fill="none" stroke="#222" stroke-width="1.8" stroke-linejoin="round"><path d="M12 2.5l2.9 6.1 6.6.8-4.9 4.6 1.3 6.6L12 17.3l-5.9 3.3 1.3-6.6-4.9-4.6 6.6-.8z"/></svg>
        FAVOURITES</a>
    </nav>
  </header>

  <nav class="tabs">
    <div class="tab is-active">EQUITIES</div>
    <div class="tab">ETFS</div>
    <div class="tab">PAIRS</div>
    <div class="tab">ETF PAIRS</div>
    <div class="tab">FACTORS</div>
    <div class="tab">NEW TAB TITLE #1</div>
    <div class="tab">NEW TAB TITLE #2</div>
    <div class="tab tab-more">
      <svg width="12" height="18" viewBox="0 0 12 18" fill="none" stroke="#888" stroke-width="3"><path d="M2 2l7 7-7 7"/></svg>
    </div>
    <div class="tab-add">
      <svg width="22" height="22" viewBox="0 0 22 22" fill="none" stroke="#fff" stroke-width="1.6"><circle cx="11" cy="11" r="9.5"/><path d="M11 6v10M6 11h10"/></svg>
    </div>
  </nav>

  <section class="panel">
    <div class="filters">
      <label>Quality <b>Threshold:</b><input class="field" type="text" value="-10"></label>
      <label class="abs"><b style="margin-left:0;margin-right:4px">Abs.</b> Stat <b>Threshold:</b><input class="field" type="text" value="-10"></label>
      <a href="#" class="export">
        <svg width="24" height="22" viewBox="0 0 24 22" fill="none" stroke="#1a3f87" stroke-width="2.2" stroke-linecap="round" stroke-linejoin="round"><path d="M11 4H4a2 2 0 0 0-2 2v12a2 2 0 0 0 2 2h12a2 2 0 0 0 2-2v-5"/><path d="M9 13c2-6 6-8 12-8"/><path d="M17 2l4 3-3 4"/></svg>
        Export</a>
    </div>

    <table class="models">
      <colgroup>
        <col style="width:92px"><col style="width:102px"><col style="width:106px"><col style="width:106px">
        <col style="width:83px"><col style="width:83px"><col style="width:83px"><col style="width:83px">
        <col style="width:83px"><col style="width:83px"><col style="width:83px"><col style="width:83px">
      </colgroup>
      <thead>
        <tr>
          <th class="key">ID <svg width="10" height="7" viewBox="0 0 10 7" fill="none" stroke="#fff" stroke-width="2"><path d="M1 1l4 4 4-4"/></svg></th>
          <th class="key">Sector</th>
          <th class="key">Time</th>
          <th>Quality</th><th>Stat 1</th><th>Stat 2</th><th>Stat 3</th><th>Stat 4</th>
          <th>Stat 5</th><th>Stat 6</th><th>Stat 7</th><th>Stat 8</th>
        </tr>
      </thead>
      <tbody>
        <tr><td class="id">Model 1</td><td>Materials</td><td class="time">2019-07-03<br>12:15:00.000</td><td class="num">30.2288</td><td class="num left">2.01574</td><td class="num">23.305</td><td class="num">-0.149368</td><td class="num">22.3054</td><td class="num">4.63714</td><td class="num left">0.945706</td><td class="num left">2.81949</td><td class="num">2.60858</td></tr>
        <tr><td class="id">Model 2</td><td>Industrials</td><td class="time">2019-07-03<br>12:15:00.000</td><td class="num">32.8694</td><td class="num left">0.87307</td><td class="num">32.185</td><td class="num">-0.033692</td><td class="num">33.9911</td><td class="num">11.5693</td><td class="num left">-0.472968</td><td class="num left">-0.830458</td><td class="num">6.80646</td></tr>
        <tr><td class="id">Model 3</td><td>Consumer Discretionary</td><td class="time">2019-07-03<br>12:15:00.000</td><td class="num">1.66002</td><td class="num left">-0.569222</td><td class="num">159.814</td><td class="num">0.0252328</td><td class="num">172.616</td><td class="num">10.2875</td><td class="num left">-0.750396</td><td class="num left">-0.385309</td><td class="num">4.69146</td></tr>
        <tr><td class="id">Model 4</td><td>Information Technology</td><td class="time">2019-07-03<br>12:15:00.000</td><td class="num">45.6856</td><td class="num left">0.412148</td><td class="num">202.488</td><td class="num">0.0084923</td><td class="num">205.834</td><td class="num">11.9094</td><td class="num left">-0.137913</td><td class="num left">0.449595</td><td class="num">3.85106</td></tr>
        <tr><td class="id">Model 5</td><td>Information Technology</td><td class="time">2019-07-03<br>12:15:00.000</td><td class="num">75.7733</td><td class="num left">7.06728</td><td class="num">188.605</td><td class="num">0.016913</td><td class="num">161.665</td><td class="num">3.82241</td><td class="num left">0.981019</td><td class="num left">1.29847</td><td class="num">3.34927</td></tr>
      </tbody>
    </table>
  </section>
</div>
</body>
</html>
```